IT Product Event Invitations

We are requesting the design of two invitations for a series of technological events that will be held between the company Tidewell Labs and its partner in the Dominican Republic, Corvantel.
Both events represent the launch of the Tidewell Labs brand in the Dominican Republic.
The first event is an elegant dinner aimed at the banking sector of the Dominican Republic to showcase the "Ledgerline Banking Suite" software.
Event information:
- Descriptive text for the invitation: Corvantel y Tidewell Labs le invitan a descubrir cómo reducir costos, aumentar la automatización y mejorar la satisfacción de los clientes a través de una solución única para enfrentar los desafíos de la banca.
- Date: 25 de Septiembre
- Time: 7PM
- Location: El Pimiento, Av. Julián Marcano 318
In the invitation, consider using the colors of the Tidewell Labs and Corvantel brands if possible. You can find the logos in the webpage
The second event is a wine tasting to present "Harborview Operations Hub" aimed at various industries.
Event information:
- Descriptive text for the invitation: Corvantel y Tidewell Labs le invitan a conocer una solución que le permitirá a toda su empresa brindar una experiencia de servicio a otro nivel.
- Date: 26 de Septiembre
- Time: 7PM
In the invitation, consider using the colors of the Tidewell Labs and Corvantel brands if possible. You can find the logos in the web page.
Both invitations must have a button for participant registration and that when you click on the image, it will direct you to a form.
Form for Ledgerline Banking Suite: https://signup.corvantel-events.example/ledgerline-dinner
Form for Harborview Operations Hub: https://signup.corvantel-events.example/harborview-tasting
Target Market(s)
Enterprise Customers
Industry/Entity Type
Technology
Look and feel
Each slider illustrates characteristics of the customer's brand and the style your logo design should communicate.

```html
<!DOCTYPE html>
<html lang="es">
<head>
<meta charset="utf-8">
<title>Invitaciones Corvantel y Tidewell Labs</title>
<link href="https://fonts.googleapis.com/css2?family=Allura&family=Poppins:wght@400;500;600;700;800&display=swap" rel="stylesheet">
<style>
  :root {
    --stage: #6b6b6b;
    --paper: #f7f7f7;
    --ink: #1e1e1e;
    --pill-dark: #2b2b2b;
    --orange-1: #ee5a24;
    --orange-2: #f9a534;
    --coral-soft: rgba(236, 120, 95, 0.45);
    --green-1: #3aa935;
    --green-2: #62d64e;
    --green-soft: rgba(120, 214, 96, 0.45);
    --brand-red: #d4202a;
  }
  * { box-sizing: border-box; margin: 0; padding: 0; }
  html, body { width: 1200px; height: 865px; overflow: hidden; }
  body {
    background: var(--stage);
    font-family: "Poppins", sans-serif;
    color: var(--ink);
    position: relative;
  }
  .invitation {
    position: absolute;
    top: 103px;
    width: 510px;
    height: 659px;
    background: var(--paper);
    overflow: hidden;
    box-shadow: 6px 8px 14px rgba(0,0,0,0.35);
    text-align: center;
    color: inherit;
    text-decoration: none;
    display: block;
  }
  .invitation--dinner { left: 73px; --accent-1: var(--orange-1); --accent-2: var(--orange-2); --soft: var(--coral-soft); }
  .invitation--wine { left: 618px; --accent-1: var(--green-1); --accent-2: var(--green-2); --soft: var(--green-soft); }

  .backdrop { position: absolute; inset: 0; }
  .backdrop__top {
    position: absolute; right: 0; top: 0; width: 300px; height: 330px;
    background: radial-gradient(ellipse at 100% 0%, var(--soft) 0%, rgba(255,255,255,0) 70%);
  }
  .backdrop__bottom {
    position: absolute; left: 0; bottom: 0; width: 280px; height: 330px;
    background: radial-gradient(ellipse at 0% 100%, var(--soft) 0%, rgba(255,255,255,0) 70%);
  }

  .row { position: absolute; left: 0; right: 0; }
  .kicker { top: 57px; font-size: 13px; font-weight: 700; letter-spacing: 4px; }
  .event-title {
    top: 86px; font-family: "Allura", cursive; font-size: 82px; line-height: 1; font-weight: 400;
    background: linear-gradient(90deg, var(--accent-1), var(--accent-2));
    -webkit-background-clip: text; background-clip: text; color: transparent;
  }
  .tagline {
    top: 181px; left: 50%; right: auto; transform: translateX(-50%);
    background: var(--pill-dark); color: #fff; font-size: 13px; font-weight: 500;
    padding: 2px 12px; border-radius: 6px; white-space: nowrap;
  }
  .product { top: 210px; font-size: 18px; font-weight: 700; text-transform: uppercase; }
  .summary { top: 247px; left: 66px; right: 66px; font-size: 8.8px; line-height: 1.3; font-weight: 500; }
  .date { top: 302px; font-size: 31px; font-weight: 700; }
  .date sup { font-size: 14px; vertical-align: 13px; margin: 0 6px 0 4px; }
  .time {
    top: 350px; left: 50%; right: auto; transform: translateX(-50%);
    width: 138px; height: 28px; line-height: 28px; border-radius: 8px;
    background: linear-gradient(90deg, var(--accent-1), var(--accent-2));
    font-size: 19px; font-weight: 700;
  }
  .invitation--dinner .time { color: #fff; }
  .pin { top: 400px; height: 20px; }
  .pin svg { width: 16px; height: 20px; }
  .venue-label { top: 421px; font-size: 15px; letter-spacing: 5px; font-weight: 400; }
  .venue-address { top: 442px; font-size: 12.5px; font-weight: 600; }
  .brand { top: 502px; font-size: 17px; font-weight: 700; display: flex; justify-content: center; align-items: center; gap: 7px; }
  .brand__mark { width: 14px; height: 14px; border-radius: 50%; background: var(--brand-red); }
  .partner { top: 549px; font-size: 21px; font-weight: 600; }
  .booking {
    top: 595px; left: 50%; right: auto; transform: translateX(-50%);
    height: 20px; border-radius: 10px; background: var(--pill-dark);
    display: inline-flex; align-items: center; white-space: nowrap;
    padding-right: 10px;
  }
  .booking__button {
    height: 100%; padding: 0 8px; border-radius: 10px; font-size: 13px; font-weight: 700;
    background: linear-gradient(90deg, var(--accent-1), var(--accent-2)); line-height: 20px;
  }
  .invitation--dinner .booking__button { color: #fff; }
  .booking__link { color: #fff; font-size: 8.2px; font-weight: 500; padding-left: 7px; }
</style>
</head>
<body>

<a class="invitation invitation--dinner" href="https://signup.corvantel-events.example/ledgerline-dinner">
  <div class="backdrop">
    <div class="backdrop__top" role="img" aria-label="Facetas geométricas translúcidas en tono coral"></div>
    <div class="backdrop__bottom" role="img" aria-label="Facetas geométricas translúcidas en tono coral"></div>
  </div>
  <p class="row kicker">ESTÁ INVITADO A LA</p>
  <h1 class="row event-title">Cena Anual</h1>
  <p class="row tagline">PARA MOSTRAR EL SOFTWARE</p>
  <h2 class="row product">Ledgerline Banking Suite</h2>
  <p class="row summary">Corvantel y Tidewell Labs le invitan a descubrir cómo reducir costos, aumentar la automatización y mejorar la satisfacción de los clientes a través de una solución única para enfrentar los desafíos de la banca.</p>
  <p class="row date">25<sup>DE</sup>SEPTIEMBRE</p>
  <p class="row time">TIME: 7PM</p>
  <div class="row pin"><svg viewBox="0 0 16 20"><path d="M8 1a5.5 5.5 0 0 0-5.5 5.5C2.5 10.5 8 15 8 15s5.5-4.5 5.5-8.5A5.5 5.5 0 0 0 8 1z" fill="var(--accent-1)"/><circle cx="8" cy="6.5" r="2" fill="#fff"/><ellipse cx="8" cy="17.5" rx="5" ry="1.6" fill="none" stroke="var(--accent-1)" stroke-width="1.3"/></svg></div>
  <p class="row venue-label">VENUE</p>
  <p class="row venue-address">El Pimiento, Av. Julián Marcano 318</p>
  <div class="row brand"><span class="brand__mark"></span><span>Corvantel</span></div>
  <p class="row partner">Tidewell Labs</p>
  <div class="row booking"><span class="booking__button">BOOK NOW</span><span class="booking__link">https://signup.corvantel-events.example/ledgerline-dinner</span></div>
</a>

<a class="invitation invitation--wine" href="https://signup.corvantel-events.example/harborview-tasting">
  <div class="backdrop">
    <div class="backdrop__top" role="img" aria-label="Facetas geométricas translúcidas en tono verde"></div>
    <div class="backdrop__bottom" role="img" aria-label="Facetas geométricas translúcidas en tono verde"></div>
  </div>
  <p class="row kicker">ESTÁ INVITADO A LA</p>
  <h1 class="row event-title">Cata de Vinos</h1>
  <p class="row tagline">PARA MOSTRAR EL SOFTWARE</p>
  <h2 class="row product">Harborview Operations Hub</h2>
  <p class="row summary">Corvantel y Tidewell Labs le invitan a conocer una solución que le permitirá a toda su empresa brindar una experiencia de servicio a otro nivel</p>
  <p class="row date">26<sup>DE</sup>SEPTIEMBRE</p>
  <p class="row time">TIME: 7PM</p>
  <div class="row pin"><svg viewBox="0 0 16 20"><path d="M8 1a5.5 5.5 0 0 0-5.5 5.5C2.5 10.5 8 15 8 15s5.5-4.5 5.5-8.5A5.5 5.5 0 0 0 8 1z" fill="var(--accent-1)"/><circle cx="8" cy="6.5" r="2" fill="#fff"/><ellipse cx="8" cy="17.5" rx="5" ry="1.6" fill="none" stroke="var(--accent-1)" stroke-width="1.3"/></svg></div>
  <p class="row venue-label">VENUE</p>
  <p class="row venue-address">El Pimiento, Av. Julián Marcano 318</p>
  <div class="row brand"><span class="brand__mark"></span><span>Corvantel</span></div>
  <p class="row partner">Tidewell Labs</p>
  <div class="row booking"><span class="booking__button">BOOK NOW</span><span class="booking__link">https://signup.corvantel-events.example/harborview-tasting</span></div>
</a>

</body>
</html>
```